NZ First of it's kind solutions directory and marketplace for busy Mums needs a business card design

We need a business card design for our new nationwide business in NZ (long term plans to go global). We provide solutions to the everyday challenges that busy Mums face by connecting them with quality communities and suppliers of carefully selected, relevant products and services. We sell direct via our online marketplace. The final design should communicate our values of inclusivity, quality and smart solutions. Colours should incorporate our logo colour palette of #477077 and #6ba8b2. Our website is at https://www.brightnestmums.example

Target Market(s)

busy Mums, Age 28 – 50, female, income over $100K, location main centres NZ primarily but NZ wide. Is likely juggling work or career with a young family. Probably had hobbies which have fallen by the wayside.
-Wants to succeed in her chosen career without compromising on family life
-to successfully juggle her career without feeling like she is compromising her children
- Is time poor, something always has to give and it’s generally her health (she’ll stay up late, get stressed)
- probably ex corporate or professional career. Has discretional income

Industry/Entity Type

Business

Contact Information for Business Card

Lena Forbisher, Founder, BrightNestMums.example (Strapline Tap; Gather; Sorted), 47 Kowhai Terrace, Ellerslie, Auckland 1051, New Zealand. Mob: 021 483 517 Ph: +64 (0)9 571 4860

Font styles to use
Other font styles liked:
• Raleway, and/or Architects Daughter

Colors
00a990
33b8a4
86cfc6
cfeae6

Requirements
Must have
• the above details, streamline. the logo and colours associated with those logos
Should not have
• foil or metallic colours

```html
<!DOCTYPE html>
<html lang="en">
<head>
<meta charset="utf-8">
<title>BrightNestMums – Business Card</title>
<link rel="stylesheet" href="https://fonts.googleapis.com/css2?family=Roboto:wght@500&family=Work+Sans:wght@400;600&display=swap">
<style>
  :root {
    --brand-dark: #477077;
    --brand-light: #6ba8b2;
    --paper: #ffffff;
    --backdrop: #e0e0e0;
  }
  * { margin: 0; padding: 0; box-sizing: border-box; }
  html, body { width: 1200px; height: 897px; overflow: hidden; }
  body { background: var(--backdrop); position: relative; font-family: "Work Sans", sans-serif; }

  .card { position: absolute; left: 303px; width: 595px; height: 338px; overflow: hidden; }
  .card-front { top: 92px; background: var(--paper); }
  .card-back { top: 469px; height: 339px; background: var(--brand-dark); }

  .brand { position: absolute; display: flex; align-items: center; gap: 12px; }
  .brand-dot { border-radius: 50%; flex: none; }
  .brand-name { font-family: "Work Sans", sans-serif; font-weight: 600; letter-spacing: -0.5px; white-space: nowrap; }

  .card-front .brand { left: 32px; top: 46px; }
  .card-front .brand-dot { width: 30px; height: 30px; background: var(--brand-dark); }
  .card-front .brand-name { font-size: 34px; color: var(--brand-dark); }

  .holder { position: absolute; right: 31px; top: 160px; text-align: right; color: var(--brand-dark); }
  .holder-name { font-family: "Roboto", sans-serif; font-weight: 500; font-size: 28px; line-height: 32px; }
  .holder-role { font-size: 14.5px; letter-spacing: 0.6px; line-height: 18px; }

  .divider { position: absolute; left: 32px; top: 223px; width: 532px; height: 1px; background: var(--brand-dark); }

  .contact { position: absolute; top: 252px; color: var(--brand-dark); font-size: 14.5px; letter-spacing: 0.9px; line-height: 18.5px; list-style: none; }
  .contact-lines { left: 32px; }
  .contact-lines li { display: flex; align-items: center; gap: 6px; }
  .contact-lines svg { width: 9px; height: 9px; flex: none; }
  .contact-address { right: 31px; text-align: right; }

  .edge-bands { position: absolute; left: 0; bottom: 0; width: 595px; height: 30px; }

  .card-back .brand { left: 50%; top: 171px; transform: translate(-50%, -50%); gap: 16px; }
  .card-back .brand-dot { width: 40px; height: 40px; background: var(--paper); }
  .card-back .brand-name { font-size: 44px; color: var(--paper); }

  .back-url { position: absolute; left: 0; right: 0; top: 300px; text-align: center; color: var(--paper); font-size: 14.5px; letter-spacing: 1.2px; }
</style>
</head>
<body>

<section class="card card-front">
  <div class="brand">
    <span class="brand-dot"></span>
    <span class="brand-name">BrightNestMums</span>
  </div>

  <div class="holder">
    <p class="holder-name">Lena Forbisher</p>
    <p class="holder-role">Founder</p>
  </div>

  <div class="divider"></div>

  <ul class="contact contact-lines">
    <li>
      <svg viewBox="0 0 10 10"><rect x="2.5" y="0.8" width="5" height="8.4" rx="0.8" fill="none" stroke="#6ba8b2" stroke-width="1"/><line x1="4.2" y1="7.6" x2="5.8" y2="7.6" stroke="#6ba8b2" stroke-width="0.8"/></svg>
      <span>021 483 517</span>
    </li>
    <li>
      <svg viewBox="0 0 10 10"><path d="M2.4 0.8 L4 2.6 L3.1 3.8 C3.7 5.2 4.8 6.4 6.2 7 L7.4 6 L9.2 7.6 L8 9.2 C4.4 8.8 1.2 5.6 0.8 2 Z" fill="#6ba8b2"/></svg>
      <span>+64 (0)9 571 4860</span>
    </li>
    <li>
      <svg viewBox="0 0 10 10"><circle cx="5" cy="5" r="4.2" fill="none" stroke="#6ba8b2" stroke-width="0.9"/><ellipse cx="5" cy="5" rx="1.8" ry="4.2" fill="none" stroke="#6ba8b2" stroke-width="0.8"/><line x1="0.8" y1="5" x2="9.2" y2="5" stroke="#6ba8b2" stroke-width="0.8"/></svg>
      <span>www.brightnestmums.example</span>
    </li>
  </ul>

  <ul class="contact contact-address">
    <li>47 Kowhai Terrace, Ellerslie</li>
    <li>Auckland 1051, New Zealand</li>
  </ul>

  <svg class="edge-bands" viewBox="0 0 595 30" aria-hidden="true">
    <polygon points="0,22 314,22 306,30 0,30" fill="var(--brand-light)"/>
    <polygon points="342,1 595,1 595,30 313,30" fill="var(--brand-dark)"/>
  </svg>
</section>

<section class="card card-back">
  <div class="brand">
    <span class="brand-dot"></span>
    <span class="brand-name">BrightNestMums</span>
  </div>
  <p class="back-url">www.brightnestmums.example</p>
</section>

</body>
</html>
```